Business card design for holistic health care clinic

We need a double-sided business card design for our holistic health care clinic that integrates our logo design and also its color scheme. My business is called Valmira. It is an integrative medicine clinic. You have already done the logo for me. Please ensure an elegant and upscale design that is not cluttered, but still has all the necessary information (please see below for details).

Target Market(s)

Wellness, fitness, rehabilitation for educated, well-traveled open-minded clients who are focused on natural, organic, balanced and preventive healthcare and lifestyle.

Industry/Entity Type

Medical

Contact Information for Business Card

Modern, clean.

Number of Pages Required

1 page

Font styles to use
Serif
Sans Serif

Colors

Designer to choose colors to be used in the design.

Requirements
Must have
• Logo on one side, all other information on the other side.
• Other information should include:
• Tobias Wrenfeld - DOE, CPT, LMT
• 4100 East Marrow Drive
• Austin, TX 78119
• 512 555 0148
• 818 555 0192
• info@ValmiraHealth.example
• t.wrenfeld@ValmiraHealth.example
Nice to have
• Darker background on front - but not totally black - shaded/dark gray.

```html
<!DOCTYPE html>
<html lang="en">
<head>
<meta charset="utf-8">
<title>Valmira Business Card</title>
<link href="https://fonts.googleapis.com/css2?family=Roboto:wght@400;700&family=Roboto+Condensed:wght@700&display=swap" rel="stylesheet">
<style>
  :root {
    --backdrop: #5b4b3d;
    --card-dark: #262626;
    --card-dark-top: #222222;
    --card-dark-bottom: #2e2e2e;
    --brand-blue: #0b90cf;
    --ink-dark: #1b2630;
    --text-light: #f2f2f2;
  }
  * { box-sizing: border-box; margin: 0; padding: 0; }
  html, body {
    width: 1200px; height: 960px; overflow: hidden;
    background: var(--backdrop);
    font-family: "Roboto", Arial, sans-serif;
  }
  .stage { position: relative; width: 1200px; height: 960px; }
  .card {
    position: absolute; width: 600px; height: 342px;
    border-radius: 22px; overflow: hidden;
    background: linear-gradient(180deg, var(--card-dark-top), var(--card-dark-bottom));
  }
  .card--front { left: 314px; top: 114px; }
  .card--back { left: 312px; top: 472px; }

  .brand { position: absolute; left: 0; right: 0; text-align: center; color: var(--brand-blue); }
  .brand__name {
    display: block; font-weight: 700; letter-spacing: 1px; line-height: 1;
  }
  .brand__tagline { display: block; font-weight: 700; }
  .card--front .brand { top: 74px; }
  .card--front .brand__name { font-size: 50px; }
  .card--front .brand__tagline { font-size: 15px; margin-top: 6px; }
  .card--back .brand { top: 148px; }
  .card--back .brand__name { font-size: 56px; }
  .card--back .brand__tagline { font-size: 17px; margin-top: 8px; }

  .wave-band { position: absolute; left: 0; top: 0; width: 600px; height: 342px; }
  .wave-band path { fill: var(--brand-blue); }

  .contact { position: absolute; left: 0; right: 0; top: 220px; text-align: center; color: var(--ink-dark); }
  .contact__name {
    font-family: "Roboto Condensed", "Arial Narrow", sans-serif;
    font-weight: 700; font-size: 21px; letter-spacing: 0.3px;
  }
  .contact__creds { font-size: 12px; }
  .contact__rule { width: 30px; height: 1px; background: var(--ink-dark); margin: 6px auto 8px; }
  .contact__line { font-size: 14.5px; line-height: 20px; white-space: nowrap; }
  .contact__item { display: inline-flex; align-items: center; gap: 3px; }
  .icon { width: 12px; height: 12px; fill: var(--ink-dark); }

  .slogan {
    position: absolute; left: 0; right: 0; top: 282px; text-align: center;
    color: var(--text-light); font-size: 14.5px;
  }
</style>
</head>
<body>
<main class="stage">
  <section class="card card--front" aria-label="Card front">
    <div class="brand">
      <span class="brand__name">VALMIRA</span>
      <span class="brand__tagline">Integrative Holistic Medicine</span>
    </div>
    <svg class="wave-band" viewBox="0 0 600 342" aria-hidden="true">
      <path d="M0 194 C60 226 140 232 205 206 Q300 172 395 206 C460 232 540 226 600 194 L600 342 L0 342 Z"/>
    </svg>
    <div class="contact">
      <p><span class="contact__name">TOBIAS WRENFELD</span> <span class="contact__creds">- DOE, CPT, LMT</span></p>
      <div class="contact__rule"></div>
      <p class="contact__line">4100 East Marrow Drive, Austin, TX 78119</p>
      <p class="contact__line">
        <span class="contact__item"><svg class="icon" viewBox="0 0 24 24"><path d="M6.6 10.8a15.1 15.1 0 0 0 6.6 6.6l2.2-2.2c.3-.3.7-.4 1-.2 1.1.4 2.3.6 3.6.6.6 0 1 .4 1 1V20c0 .6-.4 1-1 1A17 17 0 0 1 3 4c0-.6.4-1 1-1h3.5c.6 0 1 .4 1 1 0 1.3.2 2.5.6 3.6.1.3 0 .7-.2 1z"/></svg>512 555 0148</span>
        <span class="contact__item"><svg class="icon" viewBox="0 0 24 24"><path d="M7 1h10a2 2 0 0 1 2 2v18a2 2 0 0 1-2 2H7a2 2 0 0 1-2-2V3a2 2 0 0 1 2-2zm0 3v14h10V4zm5 15.5a1 1 0 1 0 0 2 1 1 0 0 0 0-2z"/></svg>818 555 0192</span>
        <span class="contact__item"><svg class="icon" viewBox="0 0 24 24"><path d="M2 5h20v14H2zm2 2v.5l8 5 8-5V7zm0 2.8V17h16V9.8l-8 5z"/></svg>t.wrenfeld@ValmiraHealth.example</span>
      </p>
      <p class="contact__line">
        <span class="contact__item"><svg class="icon" viewBox="0 0 24 24"><path d="M12 2a10 10 0 1 0 0 20 10 10 0 0 0 0-20zm0 2a8 8 0 0 1 7.7 6h-4.2c-.2-2.2-.9-4.3-2-6zm-2.3.3c-1 1.7-1.6 3.6-1.8 5.7H4.3a8 8 0 0 1 5.4-5.7zM4.3 12h3.6c.2 2.1.8 4 1.8 5.7A8 8 0 0 1 4.3 12zm5.6 0h3.6c-.2 2-.8 3.8-1.8 5.4-1-1.6-1.6-3.4-1.8-5.4zm5.6 0h4.2a8 8 0 0 1-6.2 7.8c1.1-2.2 1.8-4.4 2-7.8z"/></svg>www.ValmiraHealth.example</span>
      </p>
    </div>
  </section>

  <section class="card card--back" aria-label="Card back">
    <div class="brand">
      <span class="brand__name">VALMIRA</span>
      <span class="brand__tagline">Integrative Holistic Medicine</span>
    </div>
    <p class="slogan">it’s all about you – your health, your objectives</p>
  </section>
</main>
</body>
</html>
```